Proposal for a new Label - Proposal for a new Label

New design for label, renewal of existing label for more than 10 years, we want to change the image of the label, highlighting the name QTM-R3 and giving more notoriety to the brand, keeping the rest of the information on the label, changing the location , color tone and tone, you can vary the tone of the colors, a stronger or softer orange, a darker or lighter gray, the corporate colors recognized by customers are white, orange and gray. The product is a powder additive that is used in the extraction of copper, the base is a bag of Kraf paper of 25 Kg. This product has been awarded as an innovative product, which marked a precedent in the mining industry positively impacting the quality of the copper produced. New design for label, renew existing label for more than 10 years, we want to change the image of the label, highlighting the name QTM-R3 and giving more notoriety to the brand, keeping the rest of the information on the label, changing location , font. and hue of colors, being able to be a stronger orange or a darker gray or vice versa, the corporate colors recognized by the clients are white, orange and gray. The product is a powder additive that is used in copper mining, the base is a bag of Kraf paper of 25 Kg. This product has been awarded as an innovative product, which is marked in the mining industry impacting the quality of copper produced.

Target Market(s)

Mining - Mining

Colors
f04a50
ec1f27
f59296
f68e4d
f37122
f8ba93
757575
cfcfcf
c4c4c4

Requirements
Must have
• 217mm X 330mm Highlight the brand Highlight the brand
Nice to have
• At the base of the label place the flags of the mining countries where the additive is used: Chile, Peru, Mexico, Spain, DR Congo, Zambia, Laos, Kazakhstan, Australia. At the base of the label, place the flags of the mining countries where the additive is used: Chile, Peru, Mexico, Spain, Congo DRC, Zambia, Laos, Kazakhstan, Australia. Indicate in a corner or place on the label that it is a global product. Indicate in a corner or place on the label that is a global product.

```html
<!DOCTYPE html>
<html lang="es">
<head>
<meta charset="utf-8">
<title>QTM-R3 Refinador de Grano – Etiqueta</title>
<link rel="stylesheet" href="https://fonts.googleapis.com/css2?family=Orbitron:wght@700;900&family=Roboto+Condensed:wght@400;700&family=Archivo:wght@700;900&display=swap">
<style>
  :root{
    --orange:#cb6a3b;
    --orange-soft:#e0a27f;
    --gray:#6b6b6b;
    --gray-dark:#5e5e5e;
    --white:#ffffff;
    --page:#ffffff;
  }
  *{box-sizing:border-box;margin:0;padding:0}
  html,body{width:1200px;height:750px;overflow:hidden;background:var(--page)}
  .label{position:relative;width:1200px;height:750px;font-family:"Roboto Condensed",Arial,sans-serif}
  .label-frame{position:absolute;left:9px;top:7px;width:1187px;height:742px;background:var(--orange);border-radius:34px}
  .brand-mark{position:absolute;left:318px;top:50px;display:flex;align-items:center;gap:10px;color:var(--white);font-family:"Archivo",Arial,sans-serif;font-weight:900;font-size:30px;letter-spacing:2px}
  .brand-mark .dot{width:22px;height:22px;border-radius:50%;background:var(--white)}
  .company{position:absolute;left:753px;top:28px;color:var(--white);font-family:Arial,Helvetica,sans-serif;font-weight:700;font-size:17px;line-height:19px}
  .product-name{position:absolute;left:84px;top:150px;width:1050px;height:135px}
  .hatch-band{position:absolute;left:87px;top:304px;width:640px;height:49px;background:var(--orange-soft);opacity:.75}
  .product-type{position:absolute;left:753px;top:307px;width:371px;border-top:2px solid var(--white);border-bottom:2px solid var(--white);color:var(--white);font-family:"Roboto Condensed",Arial,sans-serif;font-weight:700;font-size:37px;line-height:42px;text-align:left;padding-left:2px}
  .info-panel{position:absolute;left:24px;top:380px;width:1155px;height:358px;background:var(--white);border-radius:30px}
  .field{position:absolute;left:49px;width:222px;height:63px;background:var(--gray);border-radius:9px;padding:3px 4px 4px}
  .field-title{color:var(--white);font-size:19px;line-height:23px;text-align:center}
  .field-box{background:var(--white);border-radius:5px;height:32px}
  .field.lot{top:407px}.field.made{top:480px}.field.expiry{top:553px}
  .global-badge{position:absolute;left:49px;top:647px;width:222px;height:73px;background:var(--orange);border-radius:9px;display:flex;align-items:center;gap:10px;padding-left:10px;color:var(--white)}
  .global-badge p{font-size:18px;line-height:20px}
  .global-badge strong{font-weight:700;font-size:16px}
  .net-weight{position:absolute;left:309px;top:517px;color:var(--gray)}
  .net-weight .caption{font-family:Arial,Helvetica,sans-serif;font-size:21px}
  .net-weight .value{font-family:"Archivo",Arial,sans-serif;font-weight:900;font-size:94px;line-height:96px;letter-spacing:-1px}
  .divider{position:absolute;left:641px;top:413px;width:2px;height:234px;background:var(--orange)}
  .transport-note{position:absolute;left:660px;top:413px;width:234px;height:48px;transform-origin:0 0;transform:translate(0,234px) rotate(-90deg);color:var(--gray);font-family:Arial,Helvetica,sans-serif;font-weight:700;font-size:12.5px;line-height:16px;text-align:center}
  .safety{position:absolute;left:753px;top:408px;width:360px;color:var(--gray-dark);font-family:Arial,Helvetica,sans-serif;font-weight:700;font-size:15px;line-height:18px}
  .safety h3{font-size:15px;font-weight:700}
  .safety ul{list-style:none}
  .safety .first-aid{margin-top:10px}
  .flags{position:absolute;left:307px;top:684px;width:818px;height:38px;display:flex;justify-content:space-between}
  .flag{width:58px;height:37px;display:block}
</style>
</head>
<body>
<main class="label">
  <div class="label-frame"></div>

  <div class="brand-mark"><span class="dot"></span>ANDIVAR</div>

  <address class="company">
    SOCIEDAD ANDIVAR LTDA.<br>
    Calle Los Aromos 215 Bodega 12<br>
    Barrio Industrial Norte<br>
    ANTOFAGASTA, CHILE<br>
    Fono: 56-55-2700100 / 56-55-2700101
  </address>

  <svg class="product-name" viewBox="0 0 1050 135" aria-label="QTM-R3">
    <text x="0" y="125" textLength="1045" lengthAdjust="spacingAndGlyphs" fill="#ffffff" font-family="Orbitron, Arial, sans-serif" font-weight="900" font-size="160">QTM-R3</text>
  </svg>

  <div class="hatch-band" role="img" aria-label="Franja decorativa de líneas diagonales"></div>
  <h2 class="product-type">REFINADOR DE GRANO</h2>

  <section class="info-panel"></section>

  <div class="field lot"><div class="field-title">Lote Número:</div><div class="field-box"></div></div>
  <div class="field made"><div class="field-title">Fecha de Fabricación:</div><div class="field-box"></div></div>
  <div class="field expiry"><div class="field-title">Fecha de Vencimiento:</div><div class="field-box"></div></div>

  <div class="global-badge">
    <svg width="44" height="44" viewBox="0 0 44 44" aria-hidden="true">
      <g fill="none" stroke="#ffffff" stroke-width="2.4">
        <circle cx="22" cy="22" r="19"/>
        <ellipse cx="22" cy="22" rx="8" ry="19"/>
        <line x1="3" y1="22" x2="41" y2="22"/>
        <path d="M6 12h32M6 32h32"/>
      </g>
    </svg>
    <p>Producto de<br><strong>Exportación Global</strong></p>
  </div>

  <div class="net-weight">
    <div class="caption">Peso Neto:</div>
    <div class="value">25 Kg</div>
  </div>

  <div class="divider"></div>
  <p class="transport-note">PRODUCTO NO CLASIFICADO COMO<br>PELIGROSO, DE ACUERDO A<br>LA LEGISLACIÓN DE TRANSPORTE</p>

  <section class="safety">
    <h3>INFORMACIÓN DE SEGURIDAD:</h3>
    <ul>
      <li>- Evitar el contacto con la piel.</li>
      <li>- Evitar inhalar los polvos.</li>
      <li>- Usar protección adecuada.</li>
      <li>- Almacenar en lugar fresco y ventilado.</li>
      <li>- Derrames: recoger con material absorbente.</li>
      <li>- Incendios: usar extintores a base de polvo químico Co2, espuma o agua.</li>
    </ul>
    <h3 class="first-aid">PRIMEROS AUXILIOS</h3>
    <ul>
      <li>- Contacto con los ojos: lavar con abundante agua por lo menos durante 15 minutos.</li>
      <li>- Contacto con la piel: lavar con abundante agua y jabón.</li>
    </ul>
  </section>

  <div class="flags">
    <svg class="flag" viewBox="0 0 60 38" role="img" aria-label="Chile"><rect width="60" height="19" fill="#fff"/><rect y="19" width="60" height="19" fill="#d52b1e"/><rect width="22" height="19" fill="#0039a6"/><circle cx="11" cy="9.5" r="3.5" fill="#fff"/></svg>
    <svg class="flag" viewBox="0 0 60 38" role="img" aria-label="Perú"><rect width="60" height="38" fill="#fff"/><rect width="20" height="38" fill="#d91023"/><rect x="40" width="20" height="38" fill="#d91023"/></svg>
    <svg class="flag" viewBox="0 0 60 38" role="img" aria-label="México"><rect width="60" height="38" fill="#fff"/><rect width="20" height="38" fill="#006847"/><rect x="40" width="20" height="38" fill="#ce1126"/></svg>
    <svg class="flag" viewBox="0 0 60 38" role="img" aria-label="España"><rect width="60" height="38" fill="#c60b1e"/><rect y="9.5" width="60" height="19" fill="#ffc400"/></svg>
    <svg class="flag" viewBox="0 0 60 38" role="img" aria-label="República Democrática del Congo"><rect width="60" height="38" fill="#007fff"/><path d="M0 32 L52 0 H60 V6 L8 38 H0Z" fill="#f7d618"/><path d="M0 35 L56 0 H60 V3 L4 38 H0Z" fill="#ce1021"/></svg>
    <svg class="flag" viewBox="0 0 60 38" role="img" aria-label="Zambia"><rect width="60" height="38" fill="#198a00"/><rect x="40" y="14" width="6.6" height="24" fill="#de2010"/><rect x="46.6" y="14" width="6.7" height="24" fill="#000"/><rect x="53.3" y="14" width="6.7" height="24" fill="#ef7d00"/></svg>
    <svg class="flag" viewBox="0 0 60 38" role="img" aria-label="Laos"><rect width="60" height="38" fill="#ce1126"/><rect y="9.5" width="60" height="19" fill="#002868"/><circle cx="30" cy="19" r="7" fill="#fff"/></svg>
    <svg class="flag" viewBox="0 0 60 38" role="img" aria-label="Australia"><rect width="60" height="38" fill="#00247d"/><path d="M0 0L30 19M30 0L0 19" stroke="#fff" stroke-width="4"/><path d="M15 0V19M0 9.5H30" stroke="#fff" stroke-width="6"/><path d="M15 0V19M0 9.5H30" stroke="#cf142b" stroke-width="3"/><circle cx="15" cy="29" r="3" fill="#fff"/><circle cx="46" cy="10" r="2" fill="#fff"/><circle cx="52" cy="20" r="2" fill="#fff"/><circle cx="46" cy="31" r="2" fill="#fff"/></svg>
    <svg class="flag" viewBox="0 0 60 38" role="img" aria-label="Kazajistán"><rect width="60" height="38" fill="#00afca"/><circle cx="30" cy="17" r="6" fill="#fec50c"/></svg>
  </div>
</main>
</body>
</html>
```